CREATE A 2 layout and logo ( servanilo )

I need to create 2 layout for my company being a homepage will be like and other client control panel and need to create the logo of the company, my company works with website hosting and sale of dedicated server and VPS cloud the company name and servanilo, I want the site to be very accessible and that is not too flashy

Target Market(s)

website hosting

Industry/Entity Type

It Company

Number of Pages Required

2 page

Font styles to use
Sans Serif

Requirements
Must have
• domain servanilo.example
Nice to have
• banners, login area, login webmail
Should not have
• no preference

```html
<!DOCTYPE html>
<html lang="en">
<head>
<meta charset="utf-8">
<title>Servanilo — Website Hosting, Dedicated Servers &amp; VPS Cloud</title>
<link href="https://fonts.googleapis.com/css2?family=Open+Sans:ital,wght@0,400;0,600;0,700;0,800;1,400&display=swap" rel="stylesheet">
<style>
  :root {
    --orange: #e8621c;
    --ink: #333333;
    --text: #555555;
    --bar: #3a3a3a;
    --band-top: #3c3c3c;
    --band-bottom: #1f1f1f;
    --card: #e6e6e6;
    --strip: #e9e9e9;
    --white: #ffffff;
    --footer: #3b3b3b;
  }
  * { box-sizing: border-box; margin: 0; padding: 0; }
  html, body { width: 807px; height: 1200px; overflow: hidden; }
  body { position: relative; font-family: "Open Sans", Arial, sans-serif; color: var(--text); background: var(--white); }
  .abs { position: absolute; }

  /* top bar */
  .topbar { left: 0; top: 0; width: 807px; height: 21px; background: var(--bar); }
  .greeting { left: 66px; top: 5px; font-size: 7px; line-height: 10px; font-style: italic; color: #aaa; white-space: nowrap; }
  .lang { left: 594px; top: 4px; width: 75px; height: 13px; border: 1px solid #666; background: #4a4a4a; font-size: 6.5px; line-height: 10px; color: #ccc; padding: 0 0 0 20px; }
  .lang .flag { position: absolute; left: 4px; top: 3px; width: 11px; height: 6px; background: #ccc; }
  .lang .caret { position: absolute; right: 5px; top: 4px; width: 0; height: 0; border: 3px solid transparent; border-top-color: #ccc; }
  .social-top { left: 681px; top: 6px; display: flex; gap: 7px; }
  .social-top span { width: 9px; height: 9px; border-radius: 50%; background: #8a8a8a; }

  /* header */
  .logo { left: 66px; top: 43px; font-size: 18px; line-height: 22px; font-weight: 800; color: var(--ink); letter-spacing: 0.3px; }
  .nav { top: 50px; font-size: 7.5px; line-height: 10px; font-weight: 600; color: var(--ink); }
  .nav.active { color: var(--orange); }
  .signup { left: 688px; top: 43px; width: 53px; height: 22px; background: var(--orange); color: var(--white); font-size: 7.5px; display: flex; align-items: center; justify-content: center; gap: 4px; border-radius: 1px; }

  /* hero */
  .hero { left: 0; top: 84px; width: 807px; height: 340px; background: linear-gradient(180deg, #3a3f45 0%, #2a2d31 55%, #4a4d50 100%); }
  .hero-photo { left: 60px; top: 108px; width: 230px; height: 316px; background: linear-gradient(180deg, #6a6a6a 0%, #2b2b2b 60%, #1c1c1c 100%); border-radius: 90px 90px 0 0; }
  .hero-title { left: 362px; top: 188px; font-size: 34px; line-height: 44px; font-weight: 800; color: var(--white); letter-spacing: 0.5px; white-space: nowrap; }
  .hero-sub { left: 362px; top: 238px; font-size: 17px; line-height: 22px; font-weight: 600; color: var(--white); white-space: nowrap; }
  .hero-btn { left: 362px; top: 281px; width: 112px; height: 32px; background: var(--orange); color: var(--white); font-size: 9.5px; font-weight: 700; display: flex; align-items: center; justify-content: center; }
  .slide-arrow { top: 240px; width: 24px; height: 24px; border-radius: 50%; background: rgba(255,255,255,0.25); }

  /* welcome */
  .welcome-title { left: 66px; top: 454px; font-size: 15px; line-height: 20px; font-weight: 700; color: var(--ink); }
  .welcome-lead { left: 66px; top: 480px; width: 485px; font-size: 9.5px; line-height: 18px; text-align: justify; }
  .network-art { left: 66px; top: 532px; width: 170px; height: 83px; background: radial-gradient(ellipse at center, #d8d8e6 0%, #f2f2f2 70%); }
  .welcome-body { left: 259px; top: 536px; width: 287px; font-size: 7.5px; line-height: 14.5px; text-align: justify; }
  .btn-small { height: 19px; background: var(--orange); color: var(--white); font-size: 7px; display: flex; align-items: center; justify-content: center; border-radius: 1px; }

  .login { left: 582px; top: 459px; width: 159px; height: 158px; border: 1px solid #ddd; box-shadow: 0 1px 3px rgba(0,0,0,0.15); background: var(--white); }
  .login .head { height: 21px; background: var(--bar); color: var(--white); font-size: 8.5px; line-height: 11px; font-weight: 700; padding: 5px 0 0 17px; }
  .login .note { position: absolute; left: 17px; top: 28px; font-size: 6.5px; font-style: italic; }
  .login .field { position: absolute; left: 17px; width: 127px; height: 18px; border: 1px solid #ccc; font-size: 6.5px; line-height: 9px; padding: 4px 0 0 6px; }
  .login .btn-small { position: absolute; left: 17px; top: 129px; width: 44px; }

  /* offer band */
  .offer { left: 0; top: 663px; width: 807px; height: 85px; background: linear-gradient(180deg, var(--band-top), var(--band-bottom)); }
  .offer-title { left: 66px; top: 677px; font-size: 13px; line-height: 18px; font-weight: 600; color: var(--orange); white-space: nowrap; }
  .offer-text { left: 66px; top: 703px; width: 570px; font-size: 7px; line-height: 14px; color: #eeeeee; }
  .buy { left: 674px; top: 693px; width: 67px; height: 25px; border: 1px solid var(--orange); color: var(--orange); font-size: 9px; display: flex; align-items: center; justify-content: center; }

  /* services */
  .services-title { left: 0; top: 780px; width: 807px; text-align: center; font-size: 15px; line-height: 20px; font-weight: 700; color: var(--ink); }
  .services-sub { left: 0; top: 809px; width: 807px; text-align: center; font-size: 9.5px; line-height: 14px; }
  .card { top: 882px; width: 208px; height: 139px; background: var(--card); text-align: center; }
  .card h4 { margin-top: 33px; font-size: 10.5px; line-height: 14px; font-weight: 600; color: var(--ink); }
  .card p { margin: 8px auto 0; width: 180px; font-size: 7px; line-height: 14px; }
  .card .btn-small { position: absolute; left: 79px; top: 106px; width: 52px; }
  .badge-icon { top: 850px; width: 54px; height: 54px; border-radius: 50%; background: var(--orange); border: 3px solid #f1f1f1; display: flex; align-items: center; justify-content: center; }

  /* partners */
  .partners { left: 0; top: 1057px; width: 807px; height: 78px; background: var(--strip); }
  .partner { top: 1072px; width: 119px; height: 46px; border: 2px solid var(--white); background: #dcdcdc; }
  .partners-arrow { top: 1086px; font-size: 16px; line-height: 20px; color: #999; }

  /* footer */
  .footer { left: 0; top: 1138px; width: 807px; height: 62px; background: var(--footer); }
  .footer-links { left: 66px; top: 1153px; font-size: 7px; line-height: 10px; color: #ccc; word-spacing: 2px; }
  .copyright { left: 66px; top: 1173px; font-size: 7px; line-height: 10px; color: #ccc; }
  .connect { left: 568px; top: 1164px; font-size: 6.5px; line-height: 9px; color: #777; }
  .social-foot { left: 634px; top: 1157px; display: flex; gap: 9px; }
  .social-foot span { width: 21px; height: 21px; border-radius: 50%; border: 2px solid #777; }
</style>
</head>
<body>

<div class="abs topbar"></div>
<div class="abs greeting">Welcome To Our Site !</div>
<div class="abs lang"><span class="flag"></span>Portuguese<span class="caret"></span></div>
<div class="abs social-top"><span></span><span></span><span></span><span></span></div>

<div class="abs logo">SERVANILO</div>
<div class="abs nav active" style="left:326px">HOME</div>
<div class="abs nav" style="left:378px">ABOUT</div>
<div class="abs nav" style="left:433px">HOSTING</div>
<div class="abs nav" style="left:495px">OUR WORKS</div>
<div class="abs nav" style="left:569px">BLOG</div>
<div class="abs nav" style="left:619px">CONTACTS</div>
<div class="abs signup">
  <svg width="7" height="8" viewBox="0 0 7 8"><circle cx="3.5" cy="2" r="2" fill="#fff"/><path d="M0 8 Q0 4 3.5 4 Q7 4 7 8Z" fill="#fff"/></svg>Signup
</div>

<section class="abs hero" role="img" aria-label="Server room corridor with rows of racks"></section>
<div class="abs hero-photo" role="img" aria-label="Smiling businessman in a dark suit with arms crossed"></div>
<div class="abs slide-arrow" style="left:18px"><svg width="24" height="24"><path d="M14 7 L9 12 L14 17" stroke="#222" stroke-width="2.5" fill="none"/></svg></div>
<div class="abs slide-arrow" style="left:763px"><svg width="24" height="24"><path d="M10 7 L15 12 L10 17" stroke="#222" stroke-width="2.5" fill="none"/></svg></div>
<h1 class="abs hero-title">OUR COMPANY WORKS</h1>
<div class="abs hero-sub">WITH WEBSITE HOSTING...</div>
<div class="abs hero-btn">VIEW MORE INFO &nbsp;»</div>

<h2 class="abs welcome-title">WELCOME</h2>
<p class="abs welcome-lead">Simply dummy text of the printing and typesetting industry. Lorem Ipsum has been the industry's standard dummy text ever since</p>
<div class="abs network-art" role="img" aria-label="Globe connected to servers by network cables"></div>
<p class="abs welcome-body">Sed ut perspiciatis unde omnis iste natus error sit voluptatem accusantium veritatis et quasi architecto beatae vitae dicta sunt explicabo. Nemo enim ipsam quaerat voluptatem. Ut enim ad minima veniam, quis...</p>
<div class="abs btn-small" style="left:259px;top:599px;width:52px">Read More</div>

<aside class="abs login">
  <div class="head">Login Webmail</div>
  <div class="note">Login Our Website Mail!</div>
  <div class="field" style="top:48px">Name*</div>
  <div class="field" style="top:75px">E-mail*</div>
  <div class="field" style="top:102px">Password*</div>
  <div class="btn-small">Login</div>
</aside>

<section class="abs offer"></section>
<h3 class="abs offer-title">We Sale dedicated server &amp; Web Hosting !</h3>
<p class="abs offer-text">Sed ut perspiciatis unde omnis iste natus error sit voluptatem accusantium doloremque laudantium, totam rem aperiam, eaque ipsa quae ab illo inventore veritatis et quasi architecto beatae vitae dicta sunt explicabo</p>
<div class="abs buy">Buy Now!</div>

<h2 class="abs services-title">WHAT WE WORK</h2>
<p class="abs services-sub">Simply dummy text of the printing and typesetting industry. Lorem Ipsum has been the industry's standard dummy text ever since</p>

<div class="abs card" style="left:66px">
  <h4>Website Hosting</h4>
  <p>Vero eos et accusamus et iusto odio dignissimos ducimus qui blanditiis praesentium voluptatum deleniti atque corrupti quos</p>
  <div class="btn-small">Read More</div>
</div>
<div class="abs card" style="left:300px">
  <h4>Dedicated Server</h4>
  <p>Vero eos et accusamus et iusto odio dignissimos ducimus qui blanditiis praesentium voluptatum deleniti atque corrupti quos</p>
  <div class="btn-small">Read More</div>
</div>
<div class="abs card" style="left:533px">
  <h4>VPS Cloud</h4>
  <p>Vero eos et accusamus et iusto odio dignissimos ducimus qui blanditiis praesentium voluptatum deleniti atque corrupti quos</p>
  <div class="btn-small">Read More</div>
</div>

<div class="abs badge-icon" style="left:143px">
  <svg width="16" height="18" viewBox="0 0 16 18"><ellipse cx="8" cy="3" rx="7" ry="2.5" fill="#fff"/><path d="M1 6 Q8 9 15 6 V8 Q8 11 1 8Z M1 10 Q8 13 15 10 V12 Q8 15 1 12Z M1 14 Q8 17 15 14 V15 Q8 18 1 15Z" fill="#fff"/></svg>
</div>
<div class="abs badge-icon" style="left:377px">
  <svg width="18" height="14" viewBox="0 0 18 14"><rect x="0" y="0" width="18" height="4" fill="#fff"/><rect x="0" y="5" width="18" height="4" fill="#fff"/><rect x="0" y="10" width="18" height="4" fill="#fff"/><rect x="2" y="1.5" width="5" height="1" fill="#e8621c"/><rect x="2" y="6.5" width="5" height="1" fill="#e8621c"/><rect x="2" y="11.5" width="5" height="1" fill="#e8621c"/></svg>
</div>
<div class="abs badge-icon" style="left:610px">
  <svg width="20" height="14" viewBox="0 0 20 14"><path d="M5 14 Q0 14 0 10 Q0 6 4 6 Q5 1 10 1 Q15 1 16 6 Q20 6 20 10 Q20 14 15 14Z" fill="#fff"/><path d="M10 4 L6.5 8 H9 V12 H11 V8 H13.5Z" fill="#e8621c"/></svg>
</div>

<section class="abs partners"></section>
<div class="abs partners-arrow" style="left:66px">‹</div>
<div class="abs partners-arrow" style="left:731px">›</div>
<div class="abs partner" style="left:145px"></div>
<div class="abs partner" style="left:278px"></div>
<div class="abs partner" style="left:410px"></div>
<div class="abs partner" style="left:543px"></div>

<footer class="abs footer"></footer>
<nav class="abs footer-links">Home &nbsp;/&nbsp; About &nbsp;/&nbsp; Hosting &nbsp;/&nbsp; Our Works &nbsp;/&nbsp; Blog &nbsp;/&nbsp; Contacts</nav>
<div class="abs copyright">Copyrights©servanilo.2015. &nbsp;Allrights Reserved.</div>
<div class="abs connect">Connect With Us :</div>
<div class="abs social-foot"><span></span><span></span><span></span><span></span></div>

</body>
</html>
```